Calder Vane LED - E- Commerce site

We need a website designed for an LED Billboard company that sells:
1) LED Billboards (Sales & Rental)
2) LED Gas Station lights
3) Truss Systems (Sales & Rental)
4) Sound Systems (Sales & Rental)

Attached are websites that sell similar products as Calder Vane LED. Target market is for business, property managers and event coordinators.
This site will need to be an e-commerce site where customers can purchase the product directly from the site. What I'm looking for is a design layout to start.

Conceptual Web Designs:
http://192.0.2.47:8087/index.html
http://www.pmvdisplay.example/
http://www.auralomaaudio.example/
http://www.quillmarkpanel.example/

Attached is the logo of the company: Please note that the new spelling of the logo is "Calder Vane LED" using domain " CalderVaneLED.com

Industry/Entity Type

Gas Station

Number of Pages Required

5+ page

Requirements
Must have
• 1) E-Commerce - Customers will need to be able to order product from the site.
• 2) Customers will also have the option to rent the product as well.
Nice to have
• I like the image of the attached website, that has a video clip loop
• http://www.quillmarkpanel.example/

```html
<!DOCTYPE html>
<html lang="en">
<head>
<meta charset="utf-8">
<title>Calder Vane LED</title>
<link href="https://fonts.googleapis.com/css2?family=Oswald:wght@400;500&family=Roboto:wght@400;500;700&display=swap" rel="stylesheet">
<style>
:root{
  --red:#e2252b;
  --yellow:#f7c200;
  --dark:#1b1b1b;
  --darker:#141414;
  --band:#e9e9e9;
  --text:#333;
  --muted:#777;
  --line:#dcdcdc;
  --link:#2a6fc9;
}
*{box-sizing:border-box;margin:0;padding:0}
html,body{width:1200px;height:2429px;overflow:hidden}
body{font-family:"Roboto",Arial,sans-serif;color:var(--text);background:#fff;position:relative}
.wrap{position:absolute;left:131px;width:938px}
a{color:inherit;text-decoration:none}

/* header */
.site-header{position:absolute;top:0;left:0;width:1200px;height:136px;background:var(--dark)}
.top-links{position:absolute;right:131px;top:13px;display:flex;gap:30px;font-size:12px;color:#aaa;text-transform:uppercase}
.top-links .phone{color:var(--red)}
.brand{position:absolute;left:131px;top:48px;display:flex;align-items:center;gap:12px}
.brand-dot{width:40px;height:40px;border-radius:50%;background:var(--red)}
.brand-name{font-family:"Roboto",sans-serif;font-weight:700;font-size:24px;color:var(--yellow)}
.search{position:absolute;left:542px;top:60px;width:331px;height:42px;border:1px solid #444;background:#1f1f1f;display:flex;align-items:center}
.search span{flex:1;padding-left:16px;font-size:12px;font-style:italic;color:#777;text-transform:uppercase}
.search .btn{width:44px;height:100%;border-left:1px solid #444;display:flex;align-items:center;justify-content:center}
.cart{position:absolute;left:900px;top:60px;width:169px;height:42px;border:1px solid #444;display:flex;align-items:center;justify-content:center;gap:10px;font-size:12px;color:#ddd}

/* nav */
.main-nav{position:absolute;top:136px;left:0;width:1200px;height:45px;background:var(--red)}
.main-nav ul{list-style:none;display:flex;position:absolute;left:131px;height:45px}
.main-nav li{height:45px;display:flex;align-items:center;padding:0 22px;font-size:13px;color:#fff;text-transform:uppercase}
.main-nav li.active{background:var(--yellow);color:#222}

/* hero */
.hero{position:absolute;top:181px;left:0;width:1200px;height:397px;background:linear-gradient(90deg,#3a1510,#7a2a1c 25%,#2b2020 50%,#6b2a20 75%,#2a1414)}
.slide{position:absolute;left:131px;top:31px;width:938px;height:334px;background:linear-gradient(180deg,#f4f4f4,#e2e2e2 70%,#f0f0f0)}
.slide h1{position:absolute;left:31px;top:78px;font-family:"Oswald",sans-serif;font-weight:400;font-size:37px;line-height:48px;color:#222;text-transform:uppercase}
.slide h1 em{font-style:normal;color:var(--red)}
.slide .cta{position:absolute;left:33px;top:184px;width:120px;height:38px;background:var(--yellow);font-size:12px;font-weight:700;display:flex;align-items:center;justify-content:center;text-transform:uppercase;color:#222}
.slide .bulbs{position:absolute;left:390px;top:40px;width:520px;height:210px;background:radial-gradient(ellipse at center,#fbf6e6,#e6e6e6 70%)}
.arrows{position:absolute;right:16px;bottom:20px;display:flex;gap:4px}
.arrows span{width:28px;height:28px;background:var(--yellow);display:flex;align-items:center;justify-content:center}

/* categories */
.categories{top:609px;display:flex;gap:21px}
.tile{position:relative;width:219px;height:159px;overflow:hidden}
.tile .pic{position:absolute;inset:0}
.tile h2{position:absolute;left:22px;top:20px;font-family:"Roboto",sans-serif;font-weight:700;font-size:31px;line-height:1;text-transform:uppercase}
.tile p{position:absolute;left:22px;top:56px;font-size:16px;color:#fff;text-transform:uppercase;font-weight:500}
.tile .btn{position:absolute;left:22px;top:96px;width:96px;height:30px;background:var(--yellow);font-size:11px;font-weight:700;color:#222;display:flex;align-items:center;justify-content:center}
.t1 .pic{background:linear-gradient(160deg,#2a7fd4,#3b9be8 50%,#8a4a2a)}
.t1 h2{color:var(--yellow)}
.t2 .pic{background:linear-gradient(180deg,#111,#1c1c2a 60%,#4a1620)}
.t2 h2{color:var(--red)}
.t3 .pic{background:linear-gradient(120deg,#0f0f0f,#2a2a2a 70%,#555)}
.t3 h2{color:#e8246a}
.t4 .pic{background:linear-gradient(150deg,#c21fb0,#e14ad4 60%,#f2a7ea)}
.t4 h2{color:var(--yellow)}

.rule{top:800px;height:2px;background:#ddd}

/* featured */
.featured-head{top:828px;display:flex;justify-content:space-between;align-items:center;height:28px}
.featured-head h2{font-size:18px;font-weight:500;color:#222;text-transform:uppercase}
.filters{display:flex;gap:12px;font-size:12px;color:#555;text-transform:uppercase}
.filters span{padding:7px 4px}
.filters .on{background:#ddd;padding:7px 12px;color:#222}
.grid{display:grid;grid-template-columns:repeat(4,219px);column-gap:21px}
.row1{top:891px}
.row2{top:1245px}
.card{height:336px;border:1px solid var(--line);text-align:center}
.row1 .card{height:320px}
.card .pic{height:190px;border-bottom:1px solid var(--line);background:radial-gradient(circle,#e8e8e8,#fff 70%)}
.card h3{margin-top:20px;font-size:13px;font-weight:700;color:#222}
.card p{margin:10px auto 0;width:180px;font-size:12px;line-height:18px;color:var(--muted)}
.card .actions{display:flex;gap:6px;justify-content:center;margin-top:14px}
.card .actions span{width:86px;height:33px;display:flex;align-items:center;justify-content:center;font-size:11px;font-weight:700;text-transform:uppercase}
.buy{background:var(--yellow);color:#222}
.rent{background:var(--red);color:#fff}

/* values */
.values{position:absolute;top:1603px;left:0;width:1200px;height:156px;background:var(--band)}
.values .wrap{top:26px;display:grid;grid-template-columns:repeat(4,219px);column-gap:21px}
.value h3{display:flex;align-items:center;gap:10px;height:22px;font-size:16px;line-height:22px;font-weight:700;color:#222;text-transform:uppercase}
.value h3 .pct{font-size:20px;line-height:22px}
.value p{margin-top:10px;font-size:12px;line-height:18px;color:#777}
.value a{display:block;font-size:12px;color:var(--link)}

/* about */
.about{top:1791px;display:flex;justify-content:space-between}
.about h2{font-size:18px;font-weight:500;color:#222;text-transform:uppercase;letter-spacing:.3px}
.about-text{width:440px}
.about-text p{margin-top:18px;font-size:12.5px;line-height:20px;color:#666}
.about-text p+p{margin-top:4px}
.certs{width:446px}
.cert-grid{margin-top:26px;display:grid;grid-template-columns:repeat(3,120px);justify-content:space-between;row-gap:26px}
.cert-grid span{height:44px;border-radius:6px;background:#d4d4d4}

/* signup */
.signup{position:absolute;top:2029px;left:0;width:1200px;height:88px;background:var(--band)}
.signup .wrap{top:0;height:88px;display:flex;align-items:center}
.signup h4{font-size:14px;font-weight:700;color:#222;text-transform:uppercase}
.email{margin-left:22px;width:255px;height:34px;background:#fff;display:flex;align-items:center;padding-left:14px;font-size:11px;font-style:italic;color:#999}
.signup .go{width:100px;height:34px;background:var(--yellow);font-size:11px;font-weight:700;display:flex;align-items:center;justify-content:center;text-transform:uppercase}
.divider{width:1px;height:40px;background:#ccc;margin:0 38px}
.social{display:flex;gap:8px;margin-left:24px}
.social span{width:33px;height:33px}

/* footer */
.site-footer{position:absolute;top:2117px;left:0;width:1200px;height:312px;background:var(--darker)}
.foot-cols{position:absolute;top:35px;left:131px;width:938px;height:220px}
.col{position:absolute;top:0}
.col h5{font-size:12.5px;font-weight:700;color:var(--yellow);text-transform:uppercase;margin-bottom:16px}
.col li{list-style:none;font-size:12px;color:#9a9a9a;line-height:24px}
.contact li{display:flex;gap:12px;line-height:18px;margin-bottom:14px}
.contact li svg{flex:none;margin-top:2px}
.bottom-bar{position:absolute;top:255px;left:0;width:1200px;height:57px;border-top:1px solid #2a2a2a}
.bottom-bar .wrap{top:0;height:57px;display:flex;justify-content:space-between;align-items:center;font-size:11.5px;color:#999}
.pay{display:flex;align-items:center;gap:8px}
.pay i{display:block;width:32px;height:20px;border-radius:3px;background:#555}
</style>
</head>
<body>

<header class="site-header">
  <nav class="top-links">
    <span>Customer Service: <span class="phone">+123 456 7890</span></span>
    <span>My Account</span><span>Wish List (0)</span><span>Checkout</span><span>Login</span>
  </nav>
  <div class="brand"><span class="brand-dot"></span><span class="brand-name">Calder Vane LED</span></div>
  <div class="search"><span>Search here...</span>
    <div class="btn"><svg width="14" height="14" viewBox="0 0 14 14"><circle cx="6" cy="6" r="4.5" fill="none" stroke="#e2252b" stroke-width="2"/><line x1="9.5" y1="9.5" x2="13" y2="13" stroke="#e2252b" stroke-width="2"/></svg></div>
  </div>
  <div class="cart">
    <svg width="22" height="18" viewBox="0 0 22 18"><path d="M1 2h4l3 10h10l2-7H6" fill="none" stroke="#f7c200" stroke-width="2"/><circle cx="9" cy="16" r="1.6" fill="#f7c200"/><circle cx="17" cy="16" r="1.6" fill="#f7c200"/></svg>
    <span>0 ITEM(S) - $0.00</span>
  </div>
</header>

<nav class="main-nav">
  <ul>
    <li class="active">Home</li>
    <li>LED Lights Systems &nbsp;▾</li>
    <li>Truss Systems</li>
    <li>Sound Systems</li>
    <li>Service and Support</li>
    <li>About</li>
    <li>Contact Us</li>
  </ul>
</nav>

<section class="hero" role="img" aria-label="Blurred night street with illuminated signs">
  <div class="slide">
    <h1>More than<br>100 <em>LED</em> Products</h1>
    <a class="cta">Click here</a>
    <div class="bulbs" role="img" aria-label="Row of LED bulbs and spotlights on a white shelf"></div>
    <div class="arrows">
      <span><svg width="8" height="10"><path d="M7 1L2 5l5 4" fill="none" stroke="#fff" stroke-width="2"/></svg></span>
      <span><svg width="8" height="10"><path d="M1 1l5 4-5 4" fill="none" stroke="#fff" stroke-width="2"/></svg></span>
    </div>
  </div>
</section>

<section class="wrap categories">
  <div class="tile t1"><div class="pic" role="img" aria-label="LED billboard against a blue sky"></div><h2>LED</h2><p>Billboards</p><span class="btn">BUY / RENT</span></div>
  <div class="tile t2"><div class="pic" role="img" aria-label="Gas station canopy lit at night"></div><h2>LED Gas</h2><p>Station Lights</p><span class="btn">BUY NOW</span></div>
  <div class="tile t3"><div class="pic" role="img" aria-label="Close-up of loudspeakers"></div><h2>Sound</h2><p>Systems</p><span class="btn">BUY / RENT</span></div>
  <div class="tile t4"><div class="pic" role="img" aria-label="Truss stage lit in magenta"></div><h2>Truss</h2><p>Systems</p><span class="btn">BUY / RENT</span></div>
</section>

<div class="wrap rule"></div>

<div class="wrap featured-head">
  <h2>Featured Products</h2>
  <div class="filters"><span class="on">All</span><span>LED Light</span><span>Gas Station Light</span><span>Truss Systems</span><span>Sound Systems</span></div>
</div>

<section class="wrap grid row1">
  <article class="card"><div class="pic" role="img" aria-label="Recessed LED panel light"></div><h3>30W-LED Panel Light</h3><p>simply dummy text the printing and typesetting industry</p><div class="actions"><span class="buy">Buy Now</span><span class="rent">On Rent</span></div></article>
  <article class="card"><div class="pic" role="img" aria-label="LED tube"></div><h3>20W-T8-LED Tube-UL</h3><p>simply dummy text the printing and typesetting industry</p><div class="actions"><span class="buy">Buy Now</span><span class="rent">On Rent</span></div></article>
  <article class="card"><div class="pic" role="img" aria-label="Portable speaker cabinet"></div><h3>Sistema Sonido Portatil USB</h3><p>simply dummy text the printing and typesetting industry</p><div class="actions"><span class="buy">Buy Now</span><span class="rent">On Rent</span></div></article>
  <article class="card"><div class="pic" role="img" aria-label="Stage light on truss arch"></div><h3>DJ Truss arch</h3><p>simply dummy text the printing and typesetting industry</p><div class="actions"><span class="buy">Buy Now</span><span class="rent">On Rent</span></div></article>
</section>

<section class="wrap grid row2">
  <article class="card"><div class="pic" role="img" aria-label="DJ controller deck"></div><h3>Vellum QuadMix Pro</h3><p>simply dummy text the printing and typesetting industry</p><div class="actions"><span class="buy">Buy Now</span><span class="rent">On Rent</span></div></article>
  <article class="card"><div class="pic" role="img" aria-label="Square LED panel light"></div><h3>30W-LED Panel Light</h3><p>simply dummy text the printing and typesetting industry</p><div class="actions"><span class="buy">Buy Now</span><span class="rent">On Rent</span></div></article>
  <article class="card"><div class="pic" role="img" aria-label="DJ table on truss stand"></div><h3>DJ Tables &amp; Stands</h3><p>simply dummy text the printing and typesetting industry</p><div class="actions"><span class="buy">Buy Now</span><span class="rent">On Rent</span></div></article>
  <article class="card"><div class="pic" role="img" aria-label="T5 LED tubes"></div><h3>Lumora T5 LED</h3><p>simply dummy text the printing and typesetting industry</p><div class="actions"><span class="buy">Buy Now</span><span class="rent">On Rent</span></div></article>
</section>

<section class="values">
  <div class="wrap">
    <div class="value"><h3><svg width="18" height="18" viewBox="0 0 18 18"><circle cx="9" cy="9" r="6" fill="none" stroke="#222" stroke-width="4" stroke-dasharray="3 2"/><circle cx="9" cy="9" r="2.5" fill="#222"/></svg>Technology</h3><p>t is long established fact the reader will be distracted by the readable content of a page...</p><a>Read More »</a></div>
    <div class="value"><h3><span class="pct">%</span>Price</h3><p>t is long established fact the reader will be distracted by the readable content of a page...</p><a>Read More »</a></div>
    <div class="value"><h3><svg width="18" height="18" viewBox="0 0 18 18"><rect x="1" y="4" width="13" height="13" fill="none" stroke="#222" stroke-width="2"/><path d="M4 9l4 4 9-11" fill="none" stroke="#222" stroke-width="2.5"/></svg>Quality</h3><p>t is long established fact the reader will be distracted by the readable content of a page...</p><a>Read More »</a></div>
    <div class="value"><h3><svg width="18" height="18" viewBox="0 0 18 18"><circle cx="9" cy="9" r="7.5" fill="none" stroke="#222" stroke-width="2"/><path d="M9 4l1.5 3.3 3.5.3-2.7 2.3.9 3.5L9 11.5 5.8 13.4l.9-3.5L4 7.6l3.5-.3z" fill="#222"/></svg>Warranty</h3><p>t is long established fact the reader will be distracted by the readable content of a page...</p><a>Returns Policy »</a></div>
  </div>
</section>

<section class="wrap about">
  <div class="about-text">
    <h2>About Calder Vane LED</h2>
    <p>It is a long established fact that a reader will be distracted by the readable content of a page when looking at its layout. The point of using Lorem Ipsum is that it has a more-or-less normal distribution of Content here, content here, making it look like readable English.</p>
    <p>Many desktop publishing packages and web page editors now use Lorem Ipsum as their default model text, and a search for 'lorem ipsum' will uncover many web sites still in their infancy...</p>
  </div>
  <div class="certs">
    <h2>Product Certification</h2>
    <div class="cert-grid"><span></span><span></span><span></span><span></span><span></span><span></span></div>
  </div>
</section>

<section class="signup">
  <div class="wrap">
    <h4>Sign up for deals:</h4>
    <div class="email">Enter Your Email</div><span class="go">Sign Up</span>
    <div class="divider"></div>
    <h4>Stay connected:</h4>
    <div class="social"><span style="background:#3b5998"></span><span style="background:#1da1f2"></span><span style="background:#0e76a8"></span><span style="background:#dd4b39"></span></div>
  </div>
</section>

<footer class="site-footer">
  <div class="foot-cols">
    <div class="col" style="left:0"><h5>Quick Links</h5><ul><li>Home</li><li>Products</li><li>Services</li><li>About Us</li><li>FAQ's</li></ul></div>
    <div class="col" style="left:160px"><h5>Need Help?</h5><ul><li>See All Help</li><li>Returns</li><li>Shipping</li><li>Warranty</li><li>Contact Us</li></ul></div>
    <div class="col" style="left:332px"><h5>Policies &amp; Info</h5><ul><li>Terms and Conditions</li><li>Policy for Sellers</li><li>Policy for Buyers</li><li>Shipping &amp; Refund Policies</li><li>Wholesale Policy</li><li>Privacy Policy</li></ul></div>
    <div class="col" style="left:546px"><h5>My Account</h5><ul><li>Sign in</li><li>Track Order</li></ul></div>
    <div class="col contact" style="left:734px"><h5>Contact Us</h5><ul>
      <li><svg width="12" height="16" viewBox="0 0 12 16"><path d="M6 0a6 6 0 0 1 6 6c0 4-6 10-6 10S0 10 0 6a6 6 0 0 1 6-6z" fill="#888"/><circle cx="6" cy="6" r="2" fill="#141414"/></svg><span>Lorem Ipsum is simply dummy<br>Redmere, AB T0X 1A1</span></li>
      <li><svg width="12" height="14" viewBox="0 0 12 14"><path d="M2 0l3 3-1.5 2a8 8 0 0 0 4 4L9 7.5l3 3L10 13C5 13 0 8 0 2z" fill="#888"/></svg><span>Phone:<br>(123) 456 7890</span></li>
      <li><svg width="12" height="10" viewBox="0 0 12 10"><rect width="12" height="10" fill="#888"/><path d="M0 0l6 5 6-5" fill="none" stroke="#141414"/></svg><span>Email:<br>info@caldervaneled.com</span></li>
    </ul></div>
  </div>
  <div class="bottom-bar">
    <div class="wrap">
      <span>Copyright © 2016 - Calder Vane LED, All Rights Reserved</span>
      <div class="pay"><span>Accepted Payment :</span><i></i><i></i><i></i><i></i></div>
    </div>
  </div>
</footer>

</body>
</html>
```